New travel store signage for Marlow Journeys to attract luxury travellers.

Hello,
We are looking to change the signage of our stores. The signage must include the following:
1. Marlow Journeys Logo (attached)
2. The text...The Travel & Cruise Experts
3. Brand Colours ( Fb0196, 412266, d41d84 and ffffff)
Please note the signage design must be central and only cover two thirds of the store front. We have also attached an image of one of our new stores which might be helpful when preparing a mock up.

We are looking for a quick turnaround on this, making a decision within 48 hours.

Target Market(s)

Retail

Industry/Entity Type

Travel Agency

Font styles to use
Other font styles liked:
• Radley

Colors
E54698
E96AAD
F1A4CE
F9D9EA
FCEFF6
6B429C
8869AF
B7A5CE
E3DAEB
F3F0F8

Requirements
Must have
• Hello, We are looking to change the signage of our stores. The signage must include the following: 1. Marlow Journeys Logo (attached) 2. The text...The Travel & Cruise Experts 3. Brand Colours ( Fb0196, 412266, d41d84 and ffffff) Please note the signage design must be central and only cover two thirds of the store front.
Should not have
• different colour or fonts. Gradient design.

```html
<!DOCTYPE html>
<html lang="en">
<head>
<meta charset="utf-8">
<title>Marlow Journeys – Store Fascia Sign</title>
<link rel="stylesheet" href="https://fonts.googleapis.com/css2?family=Radley&display=swap">
<style>
  :root {
    --backdrop: #2f2c2d;
    --brand-pink: #e54698;
    --brand-pink-soft: #e96aad;
    --brand-blush: #f1a4ce;
    --brand-mist: #fceff6;
    --brand-violet: #8869af;
    --brand-lilac: #b7a5ce;
    --brand-deep: #412266;
    --brand-magenta: #d41d84;
    --frame-line: #2a1a3a;
  }
  * { box-sizing: border-box; margin: 0; padding: 0; }
  html, body {
    width: 1200px;
    height: 1200px;
    overflow: hidden;
    background: var(--backdrop);
  }
  .canvas {
    width: 1200px;
    height: 1200px;
    display: flex;
    align-items: center;
    justify-content: center;
  }
  .fascia-sign {
    position: relative;
    width: 1016px;
    height: 141px;
    padding: 2px;
    background: linear-gradient(90deg, var(--brand-pink-soft), var(--brand-violet));
  }
  .fascia-sign__panel {
    position: relative;
    width: 100%;
    height: 100%;
    border: 1px solid var(--frame-line);
    overflow: hidden;
  }
  .fascia-sign__backdrop {
    position: absolute;
    inset: 0;
    background:
      radial-gradient(ellipse 34% 90% at 52% 55%, rgba(252, 239, 246, 0.95), rgba(252, 239, 246, 0) 100%),
      linear-gradient(90deg,
        var(--brand-pink) 0%,
        var(--brand-pink-soft) 14%,
        var(--brand-blush) 32%,
        var(--brand-mist) 50%,
        var(--brand-lilac) 70%,
        #a870c0 84%,
        var(--brand-violet) 100%);
  }
  .brand-lockup {
    position: absolute;
    left: 50%;
    top: 50%;
    transform: translate(-50%, -50%);
    display: flex;
    flex-direction: column;
    align-items: center;
    font-family: "Radley", serif;
    color: var(--brand-deep);
  }
  .brand-lockup__name {
    font-size: 38px;
    line-height: 1;
    letter-spacing: 0.5px;
    padding-bottom: 4px;
    border-bottom: 1px solid var(--brand-deep);
  }
  .brand-lockup__tagline {
    margin-top: 4px;
    font-size: 11.5px;
    letter-spacing: 1.6px;
    text-transform: uppercase;
  }
</style>
</head>
<body>
  <main class="canvas">
    <section class="fascia-sign" aria-label="Marlow Journeys store fascia sign">
      <div class="fascia-sign__panel">
        <div class="fascia-sign__backdrop" role="img" aria-label="Soft sweeping ribbon swirls in pink fading to purple"></div>
        <div class="brand-lockup">
          <span class="brand-lockup__name">Marlow Journeys</span>
          <span class="brand-lockup__tagline">The Travel &amp; Cruise Experts</span>
        </div>
      </div>
    </section>
  </main>
</body>
</html>
```